Real estate broker business card

Want a modern celan but effective business card for my residential and commercial real estate business. I want the back of the card to advertise my services and to capture business. I have attached the back of my current business card fore ideas
Updates

Logos, photo and text updates added! Added Saturday, September 3, 2016

Project Deadline Extended Reason: LOGOS, PHOTOS AND TEST JUST UPLOADED! I'M READY TO PICK A DESIGN! THANK YOU! Added Saturday, September 3, 2016

Target Market(s)

home buyers and seller. commercial buyers and sellers

Industry/Entity Type

Real Estate

Contact Information for Business Card

must have my contact information and my photo

Requirements
Must have
• Carla Ventrino
• Owner & Qualifying Broker
• Ventrino Real Estate Services
• 505.718.2094
• carla@ventrinohomes.example
• www.ventrinohomes.example
Nice to have
• metallic
• Business capture text: " Don't buy or lease property without someone looking out for your best interests. I will represent you on your home or investment purchase for FREE!"
• "Home owners, call today to receive a FREE market analysis for your homes value!

```html
<!DOCTYPE html>
<html lang="en">
<head>
<meta charset="utf-8">
<title>Ventrino Real Estate Services – Business Card</title>
<link rel="stylesheet" href="https://fonts.googleapis.com/css2?family=Cinzel:wght@500&family=Montserrat:wght@400;500&display=swap">
<style>
  :root {
    --canvas: #e9eaec;
    --black: #050505;
    --teal: #1d8a96;
    --teal-dark: #136672;
    --steel-grey: #6d6e70;
    --ink: #1a1a1a;
    --silver-1: #8c8c8c;
    --silver-2: #f4f4f4;
    --silver-3: #b3b3b3;
    --silver-4: #e6e6e6;
    --silver-5: #7a7a7a;
  }
  * { margin: 0; padding: 0; box-sizing: border-box; }
  html, body { width: 1200px; height: 1000px; overflow: hidden; }
  body { background: var(--canvas); position: relative; font-family: "Montserrat", sans-serif; }

  .card {
    position: absolute;
    left: 278px;
    width: 644px;
    height: 377px;
    overflow: hidden;
  }
  .card--front { top: 120px; }
  .card--back { top: 539px; }
  .card svg.card-art { position: absolute; inset: 0; width: 644px; height: 377px; }

  /* Front wordmark */
  .front-brand {
    position: absolute;
    left: 0; right: 0; top: 100px;
    text-align: center;
    color: var(--teal);
    font-family: "Cinzel", serif;
    font-weight: 500;
  }
  .front-brand__dot {
    display: block;
    width: 62px; height: 62px;
    margin: 0 auto 18px;
    border-radius: 50%;
    background: var(--teal);
  }
  .front-brand__name { display: block; font-size: 46px; line-height: 1; letter-spacing: 1px; }
  .front-brand__tag { display: block; font-size: 15px; letter-spacing: 2.6px; margin-top: 8px; }

  /* Back wordmark */
  .back-brand {
    position: absolute;
    left: 44px; top: 44px;
    display: flex; align-items: center; gap: 14px;
    color: var(--teal);
    font-family: "Cinzel", serif;
    font-weight: 500;
  }
  .back-brand__dot { width: 64px; height: 64px; border-radius: 50%; background: var(--teal); flex: none; }
  .back-brand__name { display: block; font-size: 37px; line-height: 1; }
  .back-brand__tag { display: block; font-size: 12.5px; letter-spacing: 1.6px; margin-top: 6px; }

  .agent { position: absolute; left: 50px; top: 172px; }
  .agent__name {
    font-family: "Cinzel", serif; font-weight: 500;
    color: var(--teal-dark); font-size: 29px; line-height: 1;
  }
  .agent__title { font-size: 17px; color: var(--ink); margin-top: 8px; }

  .contacts { position: absolute; left: 50px; top: 274px; list-style: none; }
  .contacts li {
    display: flex; align-items: center; gap: 6px;
    font-size: 15px; color: var(--ink); height: 21px;
  }
  .contacts .icon { width: 17px; height: 17px; flex: none; }
</style>
</head>
<body>

<!-- Front of card -->
<section class="card card--front">
  <svg class="card-art" viewBox="0 0 644 377" aria-hidden="true">
    <defs>
      <linearGradient id="metal-front" x1="0" y1="0" x2="1" y2="0.6">
        <stop offset="0" stop-color="var(--silver-1)"/>
        <stop offset="0.25" stop-color="var(--silver-2)"/>
        <stop offset="0.45" stop-color="var(--silver-3)"/>
        <stop offset="0.7" stop-color="var(--silver-4)"/>
        <stop offset="1" stop-color="var(--silver-5)"/>
      </linearGradient>
    </defs>
    <rect width="644" height="377" fill="url(#metal-front)"/>
    <path d="M0,118 C150,10 300,70 430,60 C530,52 600,30 644,18 L644,262 C560,300 470,326 330,328 C200,330 90,330 0,352 Z" fill="#5a5a5a"/>
    <path d="M0,122 C150,16 300,76 430,66 C530,58 600,38 644,26 L644,256 C560,294 470,320 330,322 C200,324 90,324 0,346 Z" fill="var(--black)"/>
  </svg>
  <div class="front-brand">
    <span class="front-brand__dot"></span>
    <span class="front-brand__name">VENTRINO</span>
    <span class="front-brand__tag">REAL ESTATE SERVICES</span>
  </div>
</section>

<!-- Back of card -->
<section class="card card--back">
  <svg class="card-art" viewBox="0 0 644 377">
    <defs>
      <linearGradient id="metal-back" x1="0" y1="0" x2="1" y2="0.5">
        <stop offset="0" stop-color="var(--silver-3)"/>
        <stop offset="0.3" stop-color="var(--silver-2)"/>
        <stop offset="0.55" stop-color="var(--silver-3)"/>
        <stop offset="0.8" stop-color="var(--silver-4)"/>
        <stop offset="1" stop-color="var(--silver-5)"/>
      </linearGradient>
      <linearGradient id="ring" x1="0" y1="0" x2="0.3" y2="1">
        <stop offset="0" stop-color="#f5f5f5"/>
        <stop offset="0.4" stop-color="#8a8a8a"/>
        <stop offset="0.7" stop-color="#ededed"/>
        <stop offset="1" stop-color="#777"/>
      </linearGradient>
      <radialGradient id="portrait-tone" cx="0.5" cy="0.55" r="0.6">
        <stop offset="0" stop-color="#6a4a3a"/>
        <stop offset="0.45" stop-color="#2f2a22"/>
        <stop offset="1" stop-color="#3e5a33"/>
      </radialGradient>
      <clipPath id="portrait-clip"><circle cx="555" cy="190" r="196"/></clipPath>
    </defs>
    <rect width="644" height="377" fill="url(#metal-back)"/>
    <rect width="644" height="156" fill="var(--black)"/>
    <rect y="156" width="644" height="4" fill="#8d8d8d"/>
    <rect x="0" y="241" width="310" height="2" fill="#7d7d7d"/>
    <circle cx="555" cy="190" r="226" fill="url(#ring)"/>
    <circle cx="555" cy="190" r="212" fill="#cfcfcf"/>
    <circle cx="555" cy="190" r="204" fill="url(#ring)"/>
    <g clip-path="url(#portrait-clip)">
      <rect x="340" y="-20" width="320" height="420" fill="url(#portrait-tone)" role="img" aria-label="Portrait photo of Carla Ventrino, smiling, in front of green foliage"/>
    </g>
  </svg>

  <div class="back-brand">
    <span class="back-brand__dot"></span>
    <span>
      <span class="back-brand__name">VENTRINO</span>
      <span class="back-brand__tag">REAL ESTATE SERVICES</span>
    </span>
  </div>

  <div class="agent">
    <div class="agent__name">Carla Ventrino</div>
    <div class="agent__title">Owner &amp; Qualifying Broker</div>
  </div>

  <ul class="contacts">
    <li>
      <svg class="icon" viewBox="0 0 20 20" aria-hidden="true"><circle cx="10" cy="10" r="10" fill="var(--teal)"/><path d="M7 5.5l2 2-1 1.2c.6 1.3 1.6 2.3 2.9 2.9l1.2-1 2 2-1.3 1.4C9.5 13.8 6.2 10.5 5.9 7z" fill="#fff"/></svg>
      505.718.2094
    </li>
    <li>
      <svg class="icon" viewBox="0 0 20 20" aria-hidden="true"><circle cx="10" cy="10" r="10" fill="var(--teal)"/><rect x="5" y="6.5" width="10" height="7" fill="#fff"/><path d="M5 6.5l5 4 5-4" fill="none" stroke="var(--teal)" stroke-width="1"/></svg>
      carla@ventrinohomes.example
    </li>
    <li>
      <svg class="icon" viewBox="0 0 20 20" aria-hidden="true"><circle cx="10" cy="10" r="10" fill="var(--teal)"/><path d="M5 7l2 6 3-5 3 5 2-6" fill="none" stroke="#fff" stroke-width="1.4"/></svg>
      www.ventrinohomes.example
    </li>
  </ul>
</section>

</body>
</html>
```